Road Construction Company needs business cards

We would like a new business card designed for our business.

We're a road construction company based in Qld, Australia.

Can the business card please have the following information on it.

Name: Warren Halbeck
Position: General Manager
Phone: 0472 915 348
Email: Warren.halbeck@tovrin.com.au
Address: 87 Marrow Ave, Pendlebay, QLD, 4023
Website: www.tovrin.com.au

Visually we'd like the card to be professional and simple.

Attached is our logo.

Our website is www.tovrin.com.au

Target Market(s)

Men aged 25-60

Contact Information for Business Card

As listed in project description

Font styles to use
Serif

Requirements
Must have
• Large logo on back of card

```html
<!DOCTYPE html>
<html lang="en">
<head>
<meta charset="utf-8">
<title>Tovrin Road Construction – Business Card</title>
<link rel="stylesheet" href="https://fonts.googleapis.com/css2?family=Arimo:wght@400;700&display=swap">
<style>
  :root {
    --backdrop: #ebebeb;
    --card: #2c2c2e;
    --card-deep: #1f1f21;
    --panel-light: #3a3a3c;
    --brand-blue: #2a8ad9;
    --text-light: #e6e6e6;
    --rule: #8a8a8a;
  }
  * { box-sizing: border-box; margin: 0; padding: 0; }
  html, body {
    width: 1200px; height: 802px; overflow: hidden;
    background: var(--backdrop);
    font-family: "Arimo", Arial, sans-serif;
  }
  .stage {
    position: relative; width: 1200px; height: 802px;
    display: flex; align-items: center; justify-content: center; gap: 50px;
  }
  .card {
    position: relative; width: 540px; height: 309px;
    background: var(--card); overflow: hidden;
    box-shadow: 0 6px 18px rgba(0,0,0,.25);
  }
  /* Front */
  .front-logo {
    position: absolute; top: 62px; right: 70px;
    font-weight: 700; font-size: 40px; letter-spacing: 2px;
    color: var(--brand-blue);
  }
  .front-rule {
    position: absolute; top: 148px; left: 36px; right: 36px;
    height: 1px; background: var(--rule);
  }
  .person { position: absolute; left: 36px; top: 170px; }
  .person-name {
    font-size: 20px; color: var(--brand-blue); text-transform: uppercase;
    letter-spacing: .5px;
  }
  .person-role { font-size: 13px; color: var(--text-light); margin-top: 3px; }
  .person-divider { width: 150px; height: 1px; background: var(--rule); margin: 8px 0 9px; }
  .contact-list { list-style: none; }
  .contact-list li {
    display: flex; align-items: center; gap: 9px;
    font-size: 12.5px; color: var(--text-light); line-height: 18px;
  }
  .contact-list svg { width: 11px; height: 11px; flex: none; }
  .address {
    position: absolute; right: 36px; top: 170px;
    font-size: 13px; line-height: 18px; color: var(--text-light); text-align: left;
  }
  /* Back */
  .back-panels { position: absolute; inset: 0; }
  .back-logo {
    position: absolute; left: 34px; bottom: 40px;
    display: flex; align-items: center; gap: 10px;
    font-weight: 700; font-size: 36px; letter-spacing: 2px; color: var(--text-light);
  }
  .back-logo .mark { width: 14px; height: 14px; background: var(--brand-blue); }
</style>
</head>
<body>
<main class="stage">
  <section class="card card-front" aria-label="Business card front">
    <div class="front-logo">TOVRIN</div>
    <div class="front-rule"></div>
    <div class="person">
      <h1 class="person-name">Warren Halbeck</h1>
      <p class="person-role">General Manager</p>
      <div class="person-divider"></div>
      <ul class="contact-list">
        <li>
          <svg viewBox="0 0 12 12" aria-hidden="true"><path fill="var(--brand-blue)" d="M2.4 1l2 2-1 1.3a6.5 6.5 0 0 0 4.3 4.3L9 7.6l2 2-1.3 1.4C5 11 1 7 1 2.3z"/></svg>
          0472 915 348
        </li>
        <li>
          <svg viewBox="0 0 12 12" aria-hidden="true"><rect x="1" y="2.5" width="10" height="7" fill="none" stroke="var(--brand-blue)" stroke-width="1.2"/><path d="M1 2.5l5 4 5-4" fill="none" stroke="var(--brand-blue)" stroke-width="1.2"/></svg>
          Warren.halbeck@tovrin.com.au
        </li>
        <li>
          <svg viewBox="0 0 12 12" aria-hidden="true"><circle cx="6" cy="6" r="5" fill="var(--brand-blue)"/><path d="M1 6h10M6 1v10M2.2 3.5h7.6M2.2 8.5h7.6" stroke="var(--card)" stroke-width=".8" fill="none"/></svg>
          www.tovrin.com.au
        </li>
      </ul>
    </div>
    <address class="address" style="font-style:normal">87 Marrow Ave<br>Pendlebay, QLD, 4023</address>
  </section>

  <section class="card card-back" aria-label="Business card back">
    <svg class="back-panels" viewBox="0 0 540 309" preserveAspectRatio="none" aria-hidden="true">
      <defs>
        <linearGradient id="panelShade" x1="0" y1="0" x2="1" y2="1">
          <stop offset="0" stop-color="#151517"/>
          <stop offset="1" stop-color="#2a2a2c"/>
        </linearGradient>
      </defs>
      <rect width="540" height="309" fill="var(--card)"/>
      <polygon points="268,0 540,0 540,309 236,309" fill="url(#panelShade)"/>
      <polygon points="348,0 540,0 540,309 312,309" fill="var(--card-deep)"/>
      <line x1="348" y1="0" x2="312" y2="309" stroke="#4a4a4c" stroke-width="1"/>
    </svg>
    <div class="back-logo"><span class="mark"></span>TOVRIN</div>
  </section>
</main>
</body>
</html>
```